Small Business Broker Business Card Design

A business card design for a small business brokerage, which is a financial service, not unlike real estate brokerage, but for small businesses such as laundromats, pizza shops, restaurants, cleaners etc. The designs should all be simple, more conservative in nature, using the colors and font of the logo. Again, think real estate Brokerage as a business context
Contact Information for Business Card
Name: Glen R. Harlow. Title: Small Business Advisor. Email: g.harlow@bayfieldcapitalworks.example. Mobile: (555) 274-3918. Office: (555) 806-2147. www.bayfieldcapitalworks.example

```html
<!DOCTYPE html>
<html lang="en">
<head>
<meta charset="utf-8">
<title>Bayfield Capital Works – Business Card</title>
<link href="https://fonts.googleapis.com/css2?family=Montserrat:wght@700;800&family=Roboto:wght@400;700&family=Roboto+Condensed:wght@400&display=swap" rel="stylesheet">
<style>
  :root {
    --stage: #232323;
    --brand-green: #8dc63f;
    --brand-green-deep: #5c9e2c;
    --card-dark: #222226;
    --ink-light: #f2f2f2;
    --rule: #8a8a8e;
  }
  * { box-sizing: border-box; margin: 0; padding: 0; }
  html, body {
    width: 1200px; height: 780px; overflow: hidden;
    background: var(--stage);
  }
  .canvas {
    width: 1200px; height: 780px;
    display: flex; align-items: center; justify-content: center; gap: 40px;
  }
  .card {
    width: 540px; height: 309px;
    border-radius: 22px;
    position: relative;
    overflow: hidden;
  }

  /* Front */
  .card--front {
    background: var(--brand-green);
    display: flex; flex-direction: column; align-items: center; justify-content: center;
    gap: 10px;
    padding: 0 30px;
  }
  .brand-mark {
    display: flex; align-items: center; gap: 12px;
  }
  .brand-mark__square {
    width: 24px; height: 24px; background: var(--brand-green-deep); flex: none;
  }
  .brand-name {
    font-family: 'Montserrat', sans-serif;
    font-weight: 800;
    font-size: 24px;
    letter-spacing: 0.4px;
    color: var(--brand-green-deep);
    text-transform: uppercase;
    white-space: nowrap;
  }
  .brand-tagline {
    font-family: 'Montserrat', sans-serif;
    font-weight: 700;
    font-size: 11px;
    letter-spacing: 1.3px;
    color: var(--brand-green-deep);
    text-transform: uppercase;
    white-space: nowrap;
  }

  /* Back */
  .card--back {
    background: var(--card-dark);
    border-bottom: 5px solid var(--brand-green);
    display: flex; align-items: center;
    padding: 0 30px 0 60px;
  }
  .advisor {
    width: 200px;
    text-align: right;
    padding-right: 22px;
    padding-top: 40px;
  }
  .advisor__name {
    font-family: 'Roboto', sans-serif;
    font-weight: 700;
    font-size: 29px;
    line-height: 1.05;
    color: var(--brand-green);
    white-space: nowrap;
  }
  .advisor__title {
    font-family: 'Roboto Condensed', sans-serif;
    font-size: 14.5px;
    color: var(--ink-light);
    margin-top: 3px;
    white-space: nowrap;
  }
  .divider {
    width: 1px; height: 100px; background: var(--rule);
    margin: 0 18px 0 8px;
  }
  .contact-list { list-style: none; }
  .contact-list__item {
    display: flex; align-items: center; gap: 8px;
    font-family: 'Roboto Condensed', sans-serif;
    font-size: 12.5px;
    line-height: 1.55;
    color: var(--ink-light);
    white-space: nowrap;
  }
  .contact-list__icon { width: 12px; height: 12px; flex: none; }
</style>
</head>
<body>
<main class="canvas">

  <section class="card card--front" aria-label="Card front">
    <div class="brand-mark">
      <span class="brand-mark__square"></span>
      <span class="brand-name">Bayfield Capital Works, Inc</span>
    </div>
    <p class="brand-tagline">Steady guidance to buy or sell a local business</p>
  </section>

  <section class="card card--back" aria-label="Card back">
    <div class="advisor">
      <p class="advisor__name">Glen R. Harlow</p>
      <p class="advisor__title">Small Business Advisor</p>
    </div>
    <span class="divider"></span>
    <ul class="contact-list">
      <li class="contact-list__item">
        <svg class="contact-list__icon" viewBox="0 0 12 12" aria-hidden="true"><rect x="3" y="0.8" width="6" height="10.4" rx="1" fill="none" stroke="#8dc63f" stroke-width="1.2"/><circle cx="6" cy="9.4" r="0.6" fill="#8dc63f"/></svg>
        (555) 274-3918
      </li>
      <li class="contact-list__item">
        <svg class="contact-list__icon" viewBox="0 0 12 12" aria-hidden="true"><path d="M2.5 1 L4.5 1 L5.2 3.6 L4 4.6 Q5 7 7.4 8 L8.4 6.8 L11 7.5 L11 9.5 Q10.5 11 9 11 Q4.5 10.5 1 3 Q1 1.5 2.5 1 Z" fill="#8dc63f"/></svg>
        (555) 806-2147
      </li>
      <li class="contact-list__item">
        <svg class="contact-list__icon" viewBox="0 0 12 12" aria-hidden="true"><circle cx="6" cy="6" r="5" fill="none" stroke="#8dc63f" stroke-width="1.1"/><ellipse cx="6" cy="6" rx="2.2" ry="5" fill="none" stroke="#8dc63f" stroke-width="1"/><line x1="1" y1="6" x2="11" y2="6" stroke="#8dc63f" stroke-width="1"/></svg>
        www.bayfieldcapitalworks.example
      </li>
      <li class="contact-list__item">
        <svg class="contact-list__icon" viewBox="0 0 12 12" aria-hidden="true"><rect x="0.8" y="2.5" width="10.4" height="7.5" rx="0.8" fill="none" stroke="#8dc63f" stroke-width="1.1"/><polyline points="1,3 6,7 11,3" fill="none" stroke="#8dc63f" stroke-width="1.1"/></svg>
        g.harlow@bayfieldcapitalworks.example
      </li>
    </ul>
  </section>

</main>
</body>
</html>
```